Single-sided business card for restaurant velmora with new logo made on this site

Business card options with new logo including restaurant name, address, phone number and website. This business card is single-sided only and will be presented at the hostess desk for clients to take. I would like to see options based on a cream card background, a white card background, a yellow card background and a burgundy colored background. It needs to be elegant and traditional.

Target Market(s)

local and international crowd

Industry/Entity Type

restaurant

Contact Information for Business Card

address, website and phone number

Font styles to use
Serif

Colors
EE7325
F08F49
F5BC92
FAE3D3
FDF4ED

Requirements
Must have
• new logo, address, phone number, website
Should not have
• more than three colors

```html
<!DOCTYPE html>
<html lang="es">
<head>
<meta charset="utf-8">
<title>Velmora – Tarjeta de presentación</title>
<link href="https://fonts.googleapis.com/css2?family=Libre+Baskerville:wght@400;700&display=swap" rel="stylesheet">
<style>
  :root {
    --backdrop: #d9d9d9;
    --burgundy: #3a1a1c;
    --gold: #f2b12e;
    --cream: #fcebd0;
    --white: #ffffff;
  }
  * { box-sizing: border-box; margin: 0; padding: 0; }
  html, body {
    width: 1200px; height: 800px; overflow: hidden;
    background: var(--backdrop);
    font-family: "Libre Baskerville", "Times New Roman", serif;
  }
  .business-card {
    position: absolute; left: 100px; top: 114px;
    width: 1000px; height: 572px;
    border-radius: 36px; overflow: hidden;
    background: var(--cream);
    box-shadow: 0 18px 40px rgba(0,0,0,.18);
  }
  .card-background { position: absolute; inset: 0; width: 100%; height: 100%; }
  .brand-name {
    position: absolute; left: 80px; top: 300px;
    font-size: 52px; font-weight: 400; line-height: 1;
    color: var(--burgundy);
  }
  .contact {
    position: absolute; right: 110px; top: 140px;
    text-align: right; color: var(--white);
    display: flex; flex-direction: column; align-items: flex-end;
  }
  .contact-heading { color: var(--gold); font-weight: 700; font-size: 26px; line-height: 1.25; }
  .contact-line { font-size: 25px; line-height: 1.3; }
  .contact-heading.reservations { margin-top: 18px; }
  .phone { display: flex; align-items: center; gap: 10px; font-size: 30px; line-height: 1.3; }
  .phone svg { width: 26px; height: 26px; }
  .website {
    margin-top: 14px; background: var(--gold); color: var(--burgundy);
    font-weight: 700; font-size: 24px; padding: 6px 24px; border-radius: 22px;
  }
</style>
</head>
<body>
  <div class="business-card">
    <svg class="card-background" viewBox="0 0 1000 572" preserveAspectRatio="none" aria-hidden="true">
      <path d="M425,0 C345,130 420,230 525,300 C640,365 605,480 496,572 L1000,572 L1000,0 Z" fill="var(--gold)"/>
      <path d="M425,0 C345,130 420,230 525,300 C620,365 585,480 520,572 L1000,572 L1000,0 Z" fill="var(--burgundy)"/>
      <path d="M440,30 C420,120 470,190 560,240 C490,215 430,160 440,30 Z" fill="var(--cream)"/>
    </svg>

    <p class="brand-name">Velmora</p>

    <div class="contact">
      <p class="contact-heading">Restaurant Velmora</p>
      <p class="contact-line">Calle Jazmín 418</p>
      <p class="contact-line">Bahías de Santa Cruz</p>
      <p class="contact-line">Oaxaca CP 70912</p>
      <p class="contact-heading reservations">Reservaciones</p>
      <p class="phone">
        <svg viewBox="0 0 24 24" aria-hidden="true"><path d="M6.6 10.8a15.1 15.1 0 0 0 6.6 6.6l2.2-2.2a1 1 0 0 1 1-.25 11.4 11.4 0 0 0 3.6.57 1 1 0 0 1 1 1V20a1 1 0 0 1-1 1A17 17 0 0 1 3 4a1 1 0 0 1 1-1h3.5a1 1 0 0 1 1 1c0 1.25.2 2.45.57 3.57a1 1 0 0 1-.25 1z" fill="none" stroke="var(--white)" stroke-width="1.6"/></svg>
        958-214-3096
      </p>
      <p class="website">velmora.com.mx</p>
    </div>
  </div>
</body>
</html>
```